Business Card Design - ChoiceCraft

Looking for creative, modern design, two sided for ChoiceCraft that is consistent with color and feel of website www.choicecraftpro.net.
Updates

Back of card will be used to promote products or have a quote revolving around decisions, change, leadership, innovation, creativity. Back should also have space to promote website, but optional to use the icon. Front of the card will need to use the icon and have standard place for name, job title, phone and email. We are not looking to put a mailing address or fax. Also want space to place a few words/phrase explaining what we do...such as individual growth and organizational development or tools, training, information...in addition, want the facebook icon small on the front somewhere as we are also on facebook.

Vector file uploaded of icon.

Target Market(s)

Professional coaching for individual growth and organizational development

Industry/Entity Type

Business

Requirements
Must have
• Icon...see attached.

```html
<!DOCTYPE html>
<html lang="en">
<head>
<meta charset="utf-8">
<title>ChoiceCraft Business Card</title>
<link rel="stylesheet" href="https://fonts.googleapis.com/css2?family=Arimo:wght@400;700&family=Open+Sans:wght@400;600;700&display=swap">
<style>
  :root {
    --stage: #e4e6e8;
    --card-white: #ffffff;
    --ink: #3a3a3a;
    --ink-soft: #555b60;
    --rule: #c9ccd0;
    --blue-deep: #1a6db8;
    --blue-mid: #2a8fd6;
    --blue-light: #5cc0f0;
    --swoosh: #2b3340;
    --quote-white: #ffffff;
  }
  * { margin: 0; padding: 0; box-sizing: border-box; }
  html, body { width: 1200px; height: 392px; overflow: hidden; }
  body {
    background: var(--stage);
    position: relative;
    font-family: "Open Sans", sans-serif;
  }
  .card {
    position: absolute;
    border-radius: 22px;
    overflow: hidden;
    box-shadow: 0 2px 6px rgba(0,0,0,0.25);
  }
  /* Front */
  .card-front {
    left: 47px; top: 46px; width: 546px; height: 311px;
    background: var(--card-white);
  }
  .front-band { position: absolute; left: 0; top: 0; width: 546px; height: 311px; }
  .brand {
    position: absolute; left: 40px; top: 26px; width: 210px;
    display: flex; flex-direction: column; align-items: center;
  }
  .brand-mark {
    width: 112px; height: 112px; border-radius: 50%;
    background: radial-gradient(circle at 45% 40%, #e9f1f8, #9fc4e4 70%, var(--blue-mid));
  }
  .brand-name {
    margin-top: 24px;
    font-family: "Open Sans", sans-serif;
    font-weight: 700; font-size: 21px; color: #1e1e1e;
  }
  .divider {
    position: absolute; left: 264px; top: 98px; width: 1px; height: 120px;
    background: var(--rule);
  }
  .contact { position: absolute; left: 278px; top: 100px; }
  .person { font-size: 19px; color: var(--ink); font-weight: 700; margin-bottom: 9px; }
  .person .title { font-weight: 400; font-size: 17px; }
  .contact-list { list-style: none; }
  .contact-list li {
    display: flex; align-items: center; gap: 6px;
    font-size: 13.5px; color: var(--ink-soft); line-height: 18.5px;
  }
  .contact-list svg { width: 10px; height: 10px; flex: none; }
  .social-square { width: 9px; height: 9px; background: var(--blue-deep); flex: none; margin: 0 1px; }
  .tagline {
    position: absolute; left: 0; right: 0; bottom: 14px;
    text-align: center; color: #fff; font-size: 13.5px;
  }
  /* Back */
  .card-back {
    left: 620px; top: 44px; width: 540px; height: 305px;
    background: radial-gradient(ellipse 70% 75% at 70% 55%, var(--blue-light), var(--blue-mid) 55%, var(--blue-deep));
  }
  .quotes { list-style: none; position: absolute; left: 16px; top: 22px; width: 470px; }
  .quote { margin-bottom: 12px; font-family: "Arimo", sans-serif; color: var(--quote-white); }
  .quote-text { font-size: 14px; line-height: 18px; }
  .quote-text::before { content: "\201C"; font-weight: 700; font-size: 24px; vertical-align: -5px; margin-right: 3px; }
  .quote-text::after { content: "\201D"; font-weight: 700; font-size: 24px; vertical-align: -11px; margin-left: 1px; }
  .quote-author { font-size: 14px; padding-left: 19px; line-height: 17px; }
  .quote-author strong { font-weight: 700; }
  .back-mark {
    position: absolute; left: 360px; top: 170px; width: 112px;
    display: flex; flex-direction: column; align-items: center; opacity: 0.55;
  }
  .back-mark .brand-mark { width: 82px; height: 82px; }
  .back-mark .brand-name { margin-top: 6px; font-size: 14px; color: #fff; }
</style>
</head>
<body>
  <section class="card card-front">
    <svg class="front-band" viewBox="0 0 546 311" aria-hidden="true">
      <defs>
        <linearGradient id="bandBlue" x1="0" y1="0" x2="1" y2="0">
          <stop offset="0" stop-color="#1a6db8"/>
          <stop offset="0.5" stop-color="#3aa6e6"/>
          <stop offset="1" stop-color="#1a6db8"/>
        </linearGradient>
      </defs>
      <path d="M0 232 C150 262 340 272 546 244 L546 311 L0 311 Z" fill="url(#bandBlue)"/>
      <path d="M0 208 C110 232 260 258 390 262 C300 262 150 248 0 220 Z" fill="#2b3340"/>
      <path d="M0 222 C160 252 340 262 546 236 L546 244 C340 270 150 262 0 232 Z" fill="#ffffff"/>
    </svg>
    <div class="brand">
      <div class="brand-mark"></div>
      <div class="brand-name">ChoiceCraft</div>
    </div>
    <div class="divider"></div>
    <div class="contact">
      <p class="person">Your Name, <span class="title">Title</span></p>
      <ul class="contact-list">
        <li><svg viewBox="0 0 10 10"><path d="M2 1 L4 1 L4.6 3 L3.4 4 C4 5.4 4.8 6.2 6 6.6 L7 5.4 L9 6 L9 8 C5 9 1 5 2 1 Z" fill="#555b60"/></svg>123-456-789</li>
        <li><svg viewBox="0 0 10 10"><rect x="0.5" y="2" width="9" height="6.5" fill="#555b60"/><path d="M0.5 2 L5 5.5 L9.5 2" stroke="#fff" stroke-width="0.9" fill="none"/></svg>info@choicecraftpro.net</li>
        <li><svg viewBox="0 0 10 10"><circle cx="5" cy="5" r="4.3" stroke="#555b60" fill="none"/><ellipse cx="5" cy="5" rx="1.8" ry="4.3" stroke="#555b60" fill="none"/><path d="M0.7 5 H9.3" stroke="#555b60"/></svg>www.choicecraftpro.net</li>
        <li><span class="social-square"></span>/choicecraftpro</li>
      </ul>
    </div>
    <p class="tagline">Supporting individual growth and organizational development.</p>
  </section>

  <section class="card card-back">
    <ul class="quotes">
      <li class="quote"><p class="quote-text">Try not to become a man of success, but rather a man of value.</p><p class="quote-author">- <strong>Martin Vale</strong></p></li>
      <li class="quote"><p class="quote-text">The only constant is change.</p><p class="quote-author">- <strong>Corin Ashby</strong></p></li>
      <li class="quote"><p class="quote-text">We are what we repeatedly do. Excellence is not an act, it is a habit.</p><p class="quote-author">- <strong>Dana Holm</strong></p></li>
      <li class="quote"><p class="quote-text">Simplicity is the ultimate sophistication.</p><p class="quote-author">- <strong>Lena Marchetti</strong></p></li>
      <li class="quote"><p class="quote-text">Life is not fair - get used to it.</p><p class="quote-author">- <strong>Wes Garner</strong></p></li>
    </ul>
    <div class="back-mark">
      <div class="brand-mark"></div>
      <div class="brand-name">ChoiceCraft</div>
    </div>
  </section>
</body>
</html>
```